Graphic Design Project

We make rose petal jelly from old fashioned english roses. The jelly is sweet eaten with scones and clotted cream or as a filling in a victoria sandwich, as a topping on ice cream or thick set yogurt.
The image of the product is luxurious and decadent and very english.
We need a design for a label which has a picture of an old fashioned rose (rosa mundi or a compte de chambard) The rose must stand out clearly so the jelly is not confused with other fruit jams. The overall colour of the label should be pink and soft, with white or dark pink writing. The label needs to be fridge proof.

We also need a security strip to fit on the lid of the jar.

We need the following information on the label.
Name of our company-"Meadow Crown"
Name of Product-"Rose Petal Jelly"
Sales pitch-"With whole petals-a taste of summer, delicious on scones, as a filling in sponge cake, as a topping on ice cream or yogurt."
INGREDIENTS: Sugar, water, rose petals, lemon juice, natural jelling agent (agar-agar)
STORAGE: Store in a cool dry place, once opened keep refrigerated and consume within 4 weeks.
BEST BEFORE: See base

200g
Produced by:
MEADOW CROWN
The Larches
Pardew Lane
Brackwell
Fennshire
GL17 4RX
The label must have room for a bar code. The size of label approx 8-10cm long 5cm wide.
Updates

Hi

Just been looking at the Hartwell and Brace site and the labels they have there have the up market feel I am trying to convey. Hope that helps, its classy but not twee.

Thanks

Thanks for all submissions. I would be grateful if you googled images for 'Colourful and expensive biscuits at Hartwell Brace' The designs on the tins are the image we are trying to create. The colours are quite strong.

Thanks

Target Market(s)

older well off people who visit garden centres

Industry/Entity Type

Security

Requirements
Must have
• All writen info above and picture of old fashioned rose prferably rose a mundi. Luxury feel, very english, to appeal to older market
Pink colour sheme
Should not have
• dark or manly colours

```html
<!DOCTYPE html>
<html lang="en">
<head>
<meta charset="utf-8">
<title>Meadow Crown Rose Petal Jelly Label</title>
<link href="https://fonts.googleapis.com/css2?family=Kalam:wght@400&family=Dancing+Script:wght@600;700&display=swap" rel="stylesheet">
<style>
  :root {
    --label-cream: #f5eecb;
    --rose-deep: #d0245f;
    --rose-mid: #e87fb5;
    --rose-soft: #e99ac6;
    --barcode-white: #ffffff;
    --petal-dark: #d43a84;
    --petal-light: #f0b3d2;
    --petal-pale: #f6c2c6;
    --petal-coral: #ec8f98;
  }
  html, body {
    margin: 0;
    padding: 0;
    overflow: hidden;
    background: var(--label-cream);
  }
  .label {
    position: relative;
    width: 1200px;
    height: 601px;
    background: var(--label-cream);
    overflow: hidden;
    font-family: "Kalam", cursive;
    color: var(--rose-deep);
  }
  .pitch {
    position: absolute;
    margin: 0;
    font-size: 33px;
    letter-spacing: 1.5px;
    white-space: nowrap;
    line-height: 1;
  }
  .pitch--top { left: 193px; top: 32px; letter-spacing: 3.2px; }
  .pitch--bottom { left: 245px; top: 538px; letter-spacing: 2.2px; }
  .pitch--left {
    left: 45px; top: 302px;
    transform: translate(-50%, -50%) rotate(90deg);
  }
  .pitch--right {
    left: 1144px; top: 295px;
    letter-spacing: 3px;
    transform: translate(-50%, -50%) rotate(90deg);
  }
  .brand {
    position: absolute;
    left: 120px;
    top: 80px;
    margin: 0;
    font-family: "Dancing Script", cursive;
    font-weight: 700;
    font-size: 74px;
    line-height: 1;
    color: var(--rose-mid);
    -webkit-text-stroke: 1.5px var(--rose-deep);
    white-space: nowrap;
    transform: rotate(-2deg);
  }
  .product {
    position: absolute;
    left: 200px;
    top: 164px;
    margin: 0;
    font-family: "Dancing Script", cursive;
    font-weight: 600;
    font-size: 42px;
    line-height: 1;
    color: var(--rose-deep);
    white-space: nowrap;
  }
  .rose {
    position: absolute;
    display: block;
  }
  .rose--large { left: 80px; top: 224px; width: 312px; height: 292px; }
  .rose--small { left: 370px; top: 270px; width: 206px; height: 232px; }
  .product-info {
    position: absolute;
    left: 472px;
    top: 206px;
    width: 460px;
    height: 200px;
    transform: rotate(-90deg);
    color: var(--rose-soft);
    font-size: 17.5px;
    line-height: 23px;
    font-style: italic;
    text-align: center;
    white-space: nowrap;
  }
  .product-info p { margin: 0; }
  .product-info .producer { margin-top: 6px; }
  .barcode-space {
    position: absolute;
    left: 806px;
    top: 77px;
    width: 296px;
    height: 437px;
    background: var(--barcode-white);
  }
</style>
</head>
<body>
  <main class="label">
    <p class="pitch pitch--top">with whole petals-a taste of summer,</p>
    <p class="pitch pitch--left">as a filling in sponge cake,</p>
    <p class="pitch pitch--right">delicious on scones,</p>
    <p class="pitch pitch--bottom">as a topping on ice cream or yogurt.</p>

    <h1 class="brand">Meadow Crown</h1>
    <h2 class="product">Rose Petal Jelly</h2>

    <svg class="rose rose--large" viewBox="0 0 312 292" role="img" aria-label="Illustration of a large striped pink Rosa Mundi bloom">
      <defs>
        <radialGradient id="roseLargeTone" cx="50%" cy="45%" r="55%">
          <stop offset="0%" stop-color="var(--petal-dark)"/>
          <stop offset="100%" stop-color="var(--petal-light)"/>
        </radialGradient>
      </defs>
      <ellipse cx="156" cy="146" rx="154" ry="144" fill="url(#roseLargeTone)"/>
    </svg>

    <svg class="rose rose--small" viewBox="0 0 206 232" role="img" aria-label="Illustration of a smaller pale striped pink rose bloom">
      <defs>
        <radialGradient id="roseSmallTone" cx="50%" cy="45%" r="55%">
          <stop offset="0%" stop-color="var(--petal-coral)"/>
          <stop offset="100%" stop-color="var(--petal-pale)"/>
        </radialGradient>
      </defs>
      <ellipse cx="103" cy="116" rx="101" ry="113" fill="url(#roseSmallTone)"/>
    </svg>

    <section class="product-info">
      <p>200 g INGREDIENTS: Sugar, water, rose</p>
      <p>petals, lemon juice, natural jelling agent (agar-agar)</p>
      <p>STORAGE: Store in a cool dry place, once opened</p>
      <p>keep refrigerated and consume within 4 weeks.</p>
      <p>BEST BEFORE: See base</p>
      <p class="producer">Produced by: MEADOW CROWN</p>
      <p>The Larches, Pardew Lane Brackwell, Fennshire</p>
      <p>GL17 4RX</p>
    </section>

    <div class="barcode-space" aria-label="Space for bar code"></div>
  </main>
</body>
</html>
```